Harborline Renewal Business Card Design

Professional and clean design. The design colors should flow with the logo. Two-sided card with the website on the back which is:

www.HarborlineRenewal.example.

"Specializing in Water Damage Restoration"

On the front I need the name, email, phone, and logo.

Name: Darnell Quisby
Email: Darnell@HarborlineRenewal.example
Phone: 555-318-2046 for now

I only have the Preview and Thumbnail right now but should have the source files uploaded within a day or two.

Target Market(s)

Flood victims, home owners with water damage from busted pipes etc...

Industry/Entity Type

Business

Contact Information for Business Card

Name: Darnell Quisby

Font styles to use
Serif
Sans Serif

Requirements
Must have
• Business Card Details Info

```html
<!DOCTYPE html>
<html lang="en">
<head>
<meta charset="utf-8">
<title>Harborline Renewal Business Card</title>
<link href="https://fonts.googleapis.com/css2?family=Cinzel:wght@500&family=Open+Sans:wght@400;600;700&family=Oswald:wght@500&display=swap" rel="stylesheet">
<style>
  :root {
    --brand-blue: #2596d6;
    --brand-sky: #55c0ef;
    --card-white: #ffffff;
    --backdrop: #e4e7ea;
    --text-on-blue: #ffffff;
  }
  * { box-sizing: border-box; margin: 0; padding: 0; }
  html, body {
    width: 1200px; height: 900px; overflow: hidden;
    background: var(--backdrop);
  }
  .sheet {
    width: 1200px; height: 900px;
    display: flex; flex-direction: column; align-items: center; justify-content: center;
    gap: 46px;
  }
  .card {
    position: relative;
    width: 660px; height: 377px;
    background: var(--card-white);
    border-radius: 26px;
    overflow: hidden;
    box-shadow: 0 6px 18px rgba(0,0,0,0.12);
  }

  /* Brand side */
  .card--brand {
    display: flex; flex-direction: column; align-items: center; justify-content: center;
    color: var(--brand-blue);
  }
  .brand-lockup { display: flex; align-items: center; gap: 18px; }
  .brand-dot {
    width: 62px; height: 62px; border-radius: 50%;
    background: var(--brand-blue);
  }
  .brand-name {
    font-family: "Cinzel", Georgia, serif;
    font-weight: 500;
    font-size: 44px;
    letter-spacing: 1px;
    color: var(--brand-blue);
  }
  .tagline-row {
    margin-top: 16px;
    display: flex; align-items: center; gap: 12px;
  }
  .tagline-rule { width: 36px; height: 2px; background: var(--brand-blue); }
  .tagline {
    font-family: "Oswald", "Arial Narrow", sans-serif;
    font-weight: 500;
    font-size: 16px;
    letter-spacing: 2px;
    text-transform: uppercase;
    color: var(--brand-blue);
  }
  .brand-web {
    margin-top: 44px;
    font-family: "Open Sans", Arial, sans-serif;
    font-weight: 600;
    font-size: 17px;
    color: var(--brand-blue);
  }

  /* Contact side */
  .card--contact { font-family: "Open Sans", Arial, sans-serif; }
  .contact-band {
    position: absolute; left: 0; right: 0; bottom: 0; height: 186px;
    background: var(--brand-blue);
  }
  .contact-rule {
    position: absolute; left: 0; right: 0; bottom: 194px; height: 3px;
    background: var(--brand-blue);
  }
  .holder-name {
    position: absolute; right: 290px; top: 66px;
    white-space: nowrap;
    text-align: right;
    font-weight: 700; font-size: 26px; letter-spacing: 0.5px;
    line-height: 36px;
    text-transform: uppercase;
    color: var(--brand-blue);
  }
  .brand-seal {
    position: absolute; left: 50%; top: 192px;
    width: 150px; height: 150px; margin-left: -75px; margin-top: -75px;
    border-radius: 50%;
    background: var(--card-white);
    border: 6px solid var(--brand-blue);
    display: flex; align-items: center; justify-content: center;
    text-align: center;
  }
  .brand-seal span {
    font-family: "Cinzel", Georgia, serif;
    font-weight: 500; font-size: 19px; line-height: 1.25;
    color: var(--brand-blue);
  }
  .contact-lines {
    position: absolute; left: 28px; right: 30px; bottom: 26px;
    color: var(--text-on-blue);
    font-size: 15.5px; line-height: 1.6;
    text-align: right;
    white-space: nowrap;
  }
  .contact-phone { padding-right: 200px; }
</style>
</head>
<body>
  <main class="sheet">
    <section class="card card--brand" aria-label="Card back">
      <div class="brand-lockup">
        <div class="brand-dot"></div>
        <div class="brand-name">Harborline Renewal</div>
      </div>
      <div class="tagline-row">
        <span class="tagline-rule"></span>
        <span class="tagline">Specializing in Water Damage Restoration</span>
        <span class="tagline-rule"></span>
      </div>
      <div class="brand-web">www.HarborlineRenewal.example</div>
    </section>

    <section class="card card--contact" aria-label="Card front">
      <div class="contact-rule"></div>
      <div class="contact-band"></div>
      <div class="holder-name">Darnell Quisby</div>
      <div class="brand-seal"><span>Harborline<br>Renewal</span></div>
      <div class="contact-lines">
        <div class="contact-phone">P: 555-318-2046</div>
        <div class="contact-email-web">E: Darnell@HarborlineRenewal.example &nbsp;W: www.HarborlineRenewal.example</div>
      </div>
    </section>
  </main>
</body>
</html>
```